Upmarket Dessert Lounge needs a Business Card Design

We are an upmarket dessert lounge needing a business card to match our image.

We want something that is simple yet beautiful, feminine, classy, sophisticated and elegant. We want it to stand out and don't mind if it is bold.

The design should include our logo and colours of red or maroon with gold highlights. We don't mind if black is used.

Marlow & Quince

Target Market(s)

For those who like to indulge or treat themselves and give in to their temptations on good quality desserts.

Industry/Entity Type

Business

Requirements
Must have
• Must include our logo and our name

Marlow & Quince

M & Q

```html
<!DOCTYPE html>
<html lang="en">
<head>
<meta charset="utf-8">
<title>Marlow &amp; Quince — Business Card</title>
<link rel="stylesheet" href="https://fonts.googleapis.com/css2?family=Arimo:wght@400;700&display=swap">
<style>
  :root {
    --maroon: #7d1a1c;
    --maroon-deep: #5e1113;
    --red: #9e2326;
    --gold: #e9b97a;
    --peach: #f6cf9c;
    --paper: #ffffff;
    --ink: #2a2a2a;
    --stage: #e8e6e3;
  }
  html, body {
    margin: 0;
    padding: 0;
    width: 1200px;
    height: 951px;
    overflow: hidden;
    background: var(--stage);
    font-family: "Arimo", Arial, sans-serif;
  }
  .canvas {
    position: relative;
    width: 1200px;
    height: 951px;
  }
  .card {
    position: absolute;
    width: 540px;
    height: 310px;
    background: var(--paper);
    border-radius: 18px;
    overflow: hidden;
    box-shadow: 0 2px 6px rgba(0,0,0,0.12);
  }
  .card svg.decor {
    position: absolute;
    inset: 0;
    width: 100%;
    height: 100%;
  }
  .card-front { left: 80px; top: 110px; }
  .card-back { left: 580px; top: 520px; }

  .brand-name {
    position: absolute;
    color: var(--maroon);
    font-family: "Arimo", Arial, sans-serif;
    font-weight: 700;
    white-space: nowrap;
    letter-spacing: 1px;
  }
  .card-front .brand-name {
    left: 0; right: 0;
    top: 110px;
    text-align: center;
    font-size: 36px;
  }
  .card-front .website {
    position: absolute;
    left: 0; right: 0;
    top: 218px;
    text-align: center;
    color: var(--maroon);
    font-size: 17px;
    letter-spacing: 3px;
  }
  .card-back .brand-name {
    left: 88px;
    top: 66px;
    font-size: 24px;
  }
  .card-back .trading-name {
    position: absolute;
    right: 38px;
    top: 76px;
    color: var(--maroon);
    font-size: 20px;
  }
  .contact-list {
    position: absolute;
    left: 26px;
    top: 170px;
    margin: 0;
    padding: 0;
    list-style: none;
    color: var(--ink);
    font-size: 16px;
    line-height: 21px;
  }
  .contact-list li {
    display: flex;
    align-items: center;
    gap: 8px;
  }
  .contact-list svg { width: 14px; height: 14px; flex: none; }
  .address {
    position: absolute;
    left: 320px;
    top: 208px;
    display: flex;
    gap: 8px;
    color: var(--ink);
    font-size: 16px;
    line-height: 21px;
    font-style: normal;
  }
  .address svg { width: 14px; height: 14px; margin-top: 2px; flex: none; }
</style>
</head>
<body>
<main class="canvas">

  <!-- Front of card -->
  <section class="card card-front" aria-label="Card front">
    <svg class="decor" viewBox="0 0 540 310" preserveAspectRatio="none" aria-hidden="true">
      <path d="M0 0 H44 Q20 155 44 310 H0 Z" fill="var(--red)"/>
      <path d="M44 0 Q20 155 44 310" fill="none" stroke="var(--gold)" stroke-width="3"/>
      <path d="M540 0 H496 Q520 155 496 310 H540 Z" fill="var(--red)"/>
      <path d="M496 0 Q520 155 496 310" fill="none" stroke="var(--gold)" stroke-width="3"/>
    </svg>
    <div class="brand-name">Marlow &amp; Quince</div>
    <div class="website">www.marlowquince.com</div>
  </section>

  <!-- Back of card -->
  <section class="card card-back" aria-label="Card back">
    <svg class="decor" viewBox="0 0 540 310" preserveAspectRatio="none" aria-hidden="true">
      <path d="M0 0 H120 Q40 18 0 80 Z" fill="var(--red)"/>
      <path d="M140 0 Q50 28 0 112" fill="none" stroke="var(--peach)" stroke-width="7"/>
      <path d="M540 310 H420 Q500 292 540 230 Z" fill="var(--red)"/>
      <path d="M400 310 Q490 282 540 198" fill="none" stroke="var(--peach)" stroke-width="7"/>
    </svg>

    <div class="brand-name">Marlow &amp; Quince</div>
    <div class="trading-name">Marlow &amp; Quince</div>

    <ul class="contact-list">
      <li>
        <svg viewBox="0 0 16 16" aria-hidden="true"><path d="M4 1 L7 4 L5 6 Q7 10 10 11 L12 9 L15 12 L12 15 Q3 13 1 4 Z" fill="var(--maroon)"/></svg>
        512-555-0148
      </li>
      <li>
        <svg viewBox="0 0 16 16" aria-hidden="true"><rect x="4" y="1" width="8" height="5" fill="var(--maroon)"/><rect x="1" y="6" width="14" height="6" rx="1" fill="var(--maroon)"/><rect x="4" y="10" width="8" height="5" fill="#fff" stroke="var(--maroon)"/></svg>
        512-555-0149
      </li>
      <li>
        <svg viewBox="0 0 16 16" aria-hidden="true"><rect x="1" y="4" width="14" height="10" rx="1" fill="var(--maroon)"/><path d="M1 5 L8 10 L15 5" fill="none" stroke="#fff" stroke-width="1.2"/></svg>
        hello@marlowquince.com
      </li>
      <li>
        <svg viewBox="0 0 16 16" aria-hidden="true"><circle cx="8" cy="8" r="7" fill="var(--maroon)"/></svg>
        www.marlowquince.com
      </li>
    </ul>

    <address class="address">
      <svg viewBox="0 0 16 16" aria-hidden="true"><path d="M8 1 L15 8 H13 V15 H3 V8 H1 Z" fill="var(--maroon)"/></svg>
      <span>4100 Linden Park Rd.<br>Suite 210-88<br>Harlow, TX 78011</span>
    </address>
  </section>

</main>
</body>
</html>
```